Business Card Design Project

This is the first time we use our new logo. We need a business card that we can use both on our institutional corporate relationships and also that works for our staff that deals with consumers directly.

VELUNDA is a new company dedicated to empower consumers and to provide them with the best choices for specialized health care using the latest telemedicine technology (medicine at a distance via videoconference).

We want to print this cards in high quality materials and process. We will like designs that allow us to use UV spot varnish and other techniques that will differentiate us.

We are including Two different versions of Color logos. In addition we are including white over black background logos. Those can be used replacing the black for a color.

Please note this is the first time we will be creating any corporate materials with our new logo and colors.

Target Market(s)

34+ consumers of medium high and high socioeconomic levels.

Industry/Entity Type

Health

Requirements
Must have
• Our logo on its original colors
Should not have
• Any other graphical element or design that is not our logo

```html
<!DOCTYPE html>
<html lang="en">
<head>
<meta charset="utf-8">
<title>VELUNDA business card</title>
<link href="https://fonts.googleapis.com/css2?family=Arimo:wght@400;700&display=swap" rel="stylesheet">
<style>
  :root {
    --canvas: #e9e6e1;
    --card-dark: #111214;
    --card-dark-2: #1c1d20;
    --band-blue: #5ab4e0;
    --rule-blue: #1d6fa8;
    --brand-blue: #1f6aa6;
    --sky: #6cc3ea;
    --teal: #12a39b;
    --white: #ffffff;
  }
  * { box-sizing: border-box; margin: 0; padding: 0; }
  html, body { width: 1200px; height: 1057px; overflow: hidden; }
  body {
    background: var(--canvas);
    font-family: "Arimo", Arial, sans-serif;
    position: relative;
  }
  .card {
    position: absolute;
    left: 220px;
    width: 760px;
    height: 434px;
    overflow: hidden;
    box-shadow: 0 6px 18px rgba(0,0,0,.25);
  }
  .card--front { top: 70px; }
  .card--back { top: 553px; }
  .texture {
    position: absolute; inset: 0;
    background: radial-gradient(ellipse at 50% 45%, var(--card-dark-2) 0%, var(--card-dark) 75%);
  }
  /* front */
  .brand {
    position: absolute; left: 64px; top: 62px;
    display: flex; align-items: center; gap: 18px;
  }
  .brand__dot {
    width: 46px; height: 46px; border-radius: 50%;
    background: var(--brand-blue);
  }
  .brand__name {
    font-weight: 700; font-size: 64px; letter-spacing: 4px;
    color: var(--brand-blue);
  }
  .identity {
    position: absolute; left: 230px; top: 165px;
    color: var(--sky); font-weight: 700; font-size: 30px;
  }
  .identity__title { color: var(--teal); font-weight: 400; font-size: 22px; }
  .band {
    position: absolute; left: 0; right: 0; bottom: 0; height: 200px;
    background: var(--band-blue);
    border-top: 4px solid var(--rule-blue);
    box-shadow: 0 -6px 0 -2px var(--card-dark);
    display: flex; align-items: center;
    color: var(--white); font-size: 21px; line-height: 1.45;
  }
  .address {
    width: 330px; text-align: right; padding-right: 30px;
  }
  .divider {
    width: 1px; height: 130px; background: rgba(255,255,255,.7);
  }
  .contacts { list-style: none; padding-left: 30px; }
  .contacts li { display: flex; align-items: center; gap: 12px; }
  .contacts svg { width: 18px; height: 18px; flex: none; }
  /* back */
  .back-brand {
    position: absolute; left: 0; right: 0; top: 120px;
    display: flex; justify-content: center; align-items: center; gap: 22px;
  }
  .back-brand .brand__dot { width: 60px; height: 60px; }
  .back-brand .brand__name { font-size: 80px; }
  .back-url {
    position: absolute; left: 0; right: 0; top: 330px;
    text-align: center; color: var(--sky);
    font-size: 30px; letter-spacing: 6px;
  }
</style>
</head>
<body>
  <section class="card card--front">
    <div class="texture" role="img" aria-label="Dark woven carbon-fibre texture"></div>
    <div class="brand">
      <span class="brand__dot"></span>
      <span class="brand__name">VELUNDA</span>
    </div>
    <p class="identity">Your Name, <span class="identity__title">Title</span></p>
    <div class="band">
      <address class="address" style="font-style:normal">
        Street Name<br>City Name<br>State, City Zip Code
      </address>
      <span class="divider"></span>
      <ul class="contacts">
        <li>
          <svg viewBox="0 0 20 20"><circle cx="10" cy="10" r="9" fill="none" stroke="#fff" stroke-width="1.6"/><path d="M7 5c-1 1-1 3 1 6s4 4 5 4l1-2-2-1-1 1c-1 0-3-2-3-3l1-1-1-2z" fill="#fff"/></svg>
          012-345-6789
        </li>
        <li>
          <svg viewBox="0 0 20 20"><circle cx="10" cy="10" r="9" fill="none" stroke="#fff" stroke-width="1.6"/><path d="M7 5c-1 1-1 3 1 6s4 4 5 4l1-2-2-1-1 1c-1 0-3-2-3-3l1-1-1-2z" fill="#fff"/></svg>
          012-345-6789
        </li>
        <li>
          <svg viewBox="0 0 20 20"><rect x="2" y="5" width="16" height="11" fill="#fff"/><path d="M2 5l8 6 8-6" fill="none" stroke="#5ab4e0" stroke-width="1.5"/></svg>
          name@velunda.com
        </li>
        <li>
          <svg viewBox="0 0 20 20"><circle cx="10" cy="10" r="8" fill="none" stroke="#fff" stroke-width="1.6"/><ellipse cx="10" cy="10" rx="3.5" ry="8" fill="none" stroke="#fff" stroke-width="1.2"/><path d="M2 10h16" stroke="#fff" stroke-width="1.2"/></svg>
          www.velunda.com
        </li>
      </ul>
    </div>
  </section>

  <section class="card card--back">
    <div class="texture" role="img" aria-label="Dark woven carbon-fibre texture"></div>
    <div class="back-brand">
      <span class="brand__dot"></span>
      <span class="brand__name">VELUNDA</span>
    </div>
    <p class="back-url">www.velunda.com</p>
  </section>
</body>
</html>
```